Website Design for Employee Moral and Happiness Company

Looking for a clean website design that explains our features in a step by step manner so our visitors know exactly what our site does before logging in.

The site is called "Velrato". See logo design and video for a sample of style and an overview of what we do.

Target Market(s)

Business owners that are looking to retain employees.

Number of Pages Required

1 page

```html
<!DOCTYPE html>
<html lang="en">
<head>
<meta charset="utf-8">
<title>Velrato – Employee Morale &amp; Happiness</title>
<link rel="stylesheet" href="https://fonts.googleapis.com/css2?family=Merriweather:wght@400;700;900&family=Poppins:wght@400;500&display=swap">
<style>
:root{
  --orange:#f05a14;
  --orange-deep:#e04e0c;
  --ink:#161616;
  --body:#444;
  --muted:#777;
  --white:#fff;
  --black:#000;
}
*{box-sizing:border-box;margin:0;padding:0}
html,body{width:1200px;height:4552px;overflow:hidden;background:var(--white)}
body{font-family:'Merriweather',serif;color:var(--ink);position:relative}
.abs{position:absolute}
.accent{color:var(--orange)}
.brand{font-family:'Merriweather',serif;font-weight:700;color:var(--ink);display:flex;align-items:center;gap:10px}
.brand-dot{width:16px;height:16px;border-radius:50%;background:var(--orange)}

/* header */
.topbar{left:385px;top:0;width:815px;height:48px;background:var(--orange);clip-path:polygon(22px 0,100% 0,100% 100%,0 100%);display:flex;align-items:center;color:var(--white);font-size:13px}
.social{display:flex;gap:14px;margin-left:45px}
.social span{width:20px;height:20px;border-radius:50%;border:2px solid var(--white)}
.topbar .info{display:flex;align-items:center;gap:10px;margin-left:40px}
.topbar .sep{width:1px;height:30px;background:rgba(255,255,255,.7);margin-left:24px}
.topbar .ic{width:26px;height:26px;border-radius:50%;background:var(--white);display:flex;align-items:center;justify-content:center}
.header-logo{left:111px;top:28px;font-size:46px}
.nav{top:70px;left:0;width:1200px;height:24px;font-size:15px;font-weight:700}
.nav a{position:absolute;color:var(--ink);text-decoration:none}

/* hero */
.hero{left:0;top:113px;width:1200px;height:570px;background:linear-gradient(100deg,#b9b1a6 0%,#d8d1c6 30%,#8d8f93 60%,#c9c2b8 100%)}
.hero-title{left:111px;top:245px;font-size:60px;font-weight:900;line-height:1.05;color:#1c1c1c}
.hero-text{left:111px;top:378px;font-size:16px;line-height:1.7;color:#1c1c1c;width:330px}
.btn{background:var(--orange);color:var(--white);font-weight:700;border-radius:26px;display:flex;align-items:center;justify-content:center;box-shadow:0 4px 10px rgba(0,0,0,.2)}
.hero-btn{left:111px;top:445px;width:148px;height:50px;font-size:19px}
.hero-wave{left:0;top:610px}

/* about */
.about-photo{left:106px;top:724px}
.about-title{left:580px;top:757px;font-size:35px;font-weight:700}
.about-text{left:578px;top:810px;width:506px;font-size:16.5px;line-height:1.57;color:var(--body);text-align:justify}
.about-text p+p{margin-top:26px}
.about-btn{left:578px;top:1092px;width:150px;height:53px;font-size:19px}

/* services */
.services{left:0;top:1232px;width:1200px;height:765px;background:linear-gradient(120deg,#e8672a 0%,#d75418 40%,#e8702f 70%,#d9581b 100%)}
.sec-title{left:0;width:1200px;text-align:center;font-weight:700}
.services-title{top:1335px;font-size:35px;color:var(--white)}
.services-sub{top:1398px;font-size:16.5px;color:var(--white);line-height:1.6}
.card{top:1488px;width:294px;height:403px;background:var(--white);border-radius:80px 80px 0 0;padding:6px 6px 0}
.card-photo{height:162px;border-radius:76px 76px 0 0;background:linear-gradient(160deg,#dcd6cc,#8d8a86)}
.card h3{font-size:19px;text-align:center;margin-top:20px}
.card p{font-size:16px;line-height:1.62;text-align:center;color:#555;padding:0 20px;margin-top:10px}
.card b{color:var(--ink)}
.arrow{top:1690px}

/* testimonials */
.t-title{top:2062px;font-size:35px}
.t-quote{left:568px;top:2134px;width:64px;height:64px;border-radius:50%;background:var(--orange);display:flex;align-items:center;justify-content:center}
.t-name{top:2214px;font-size:25px}
.stars{color:#f6b70e;font-size:18px;margin-left:10px;letter-spacing:1px}
.t-text{top:2262px;left:280px;width:640px;font-size:16.5px;font-weight:700;line-height:1.67;color:#333;text-align:center}
.t-thanks{top:2398px;font-size:17px}
.t-side{font-size:16.5px;line-height:1.67;color:#999;top:2262px}
.t-side-name{top:2214px;left:1094px;font-size:26px;color:#aaa}
.dots{top:2480px;left:546px;display:flex;gap:22px}
.dots span{width:18px;height:2px;background:var(--ink)}
.dots .on{width:34px;background:var(--orange)}

/* video */
.video-band{left:0;top:2573px;width:1200px;height:630px;background:linear-gradient(120deg,#e56b2e,#d45119 50%,#e9763a)}
.video-frame{left:111px;top:2656px;width:977px;height:454px;border:6px solid #2a2a2a;background:linear-gradient(110deg,#cfc5b8 0%,#a89886 40%,#d6d0c8 70%,#b8aea0 100%)}
.video-logo{left:48px;top:30px;font-size:44px}
.play{left:452px;top:180px}

/* contact */
.c-title{top:3296px;font-size:35px}
.c-sub{top:3364px;font-family:'Poppins',sans-serif;font-size:16.5px;line-height:1.65;color:#333;font-weight:500}
.info-card{left:111px;top:3460px;width:377px;height:460px;background:var(--white);box-shadow:0 0 14px rgba(0,0,0,.15)}
.info-card h3{font-weight:400;font-size:30px;text-align:center;padding-top:34px;height:100px;border-bottom:2px solid var(--ink);letter-spacing:.5px}
.info-row{position:absolute;left:38px;display:flex;gap:14px}
.info-ic{width:36px;height:36px;border-radius:50%;background:var(--orange);display:flex;align-items:center;justify-content:center;flex:none}
.info-row h4{font-size:20px;font-weight:400;letter-spacing:.3px}
.info-row p{font-size:14.5px;color:#555;line-height:1.45}
.msg{left:542px;top:3460px;width:546px;height:460px;background:var(--orange);padding:0 30px}
.msg h3{color:var(--white);font-weight:400;font-size:30px;text-align:center;padding-top:34px;letter-spacing:.5px}
.field{background:var(--white);border-radius:6px;height:64px;font-size:14.5px;color:#555;padding:22px 34px;margin-top:11px}
.field:first-of-type{margin-top:34px}
.field.tall{height:110px}
.submit{background:var(--white);border-radius:6px;height:64px;margin-top:19px;color:var(--orange);font-weight:700;font-size:24px;display:flex;align-items:center;justify-content:center;letter-spacing:1px}

/* footer */
.footer{left:0;top:3985px;width:1200px;height:567px}
.sub-title{left:233px;top:4138px;font-size:30px;color:var(--white)}
.sub-form{left:601px;top:4135px;width:436px;height:46px;background:var(--white);display:flex;border:1px solid var(--orange)}
.sub-form span{flex:1;font-size:13px;color:#555;padding:15px 20px}
.sub-form b{width:132px;background:var(--orange);color:var(--white);font-size:14px;display:flex;align-items:center;justify-content:center;letter-spacing:1px}
.f-rule{left:111px;top:4227px;width:977px;height:1px;background:#555}
.f-col{top:4268px;color:var(--white);font-size:15px}
.f-col h4{font-size:20px;font-weight:400;margin-bottom:14px}
.f-col h4.b{font-weight:700}
.f-col li{list-style:none;line-height:1.85}
.f-col li::before{content:"→ ";font-size:12px}
.f-item{display:flex;gap:10px;margin-bottom:18px;line-height:1.45}
.f-soc{display:flex;gap:16px;margin-top:10px}
.f-soc span{width:28px;height:28px;border-radius:50%;background:var(--orange)}
.copy{left:0;top:4480px;width:1200px;display:flex;align-items:center;justify-content:center;gap:26px;color:var(--white);font-size:11px;font-weight:700}
.copy i{width:340px;height:1px;background:#bbb}
</style>
</head>
<body>

<!-- header -->
<div class="abs topbar">
  <div class="social"><span></span><span></span><span></span><span></span></div>
  <div class="info">
    <div class="ic"><svg width="16" height="12" viewBox="0 0 16 12"><rect x="1" y="1" width="14" height="10" fill="none" stroke="#f05a14" stroke-width="1.6"/><path d="M1 1l7 6 7-6" fill="none" stroke="#f05a14" stroke-width="1.6"/></svg></div>
    <span>Email: info@velratomail.com</span>
  </div>
  <div class="sep"></div>
  <div class="info" style="margin-left:14px">
    <div class="ic"><svg width="14" height="14" viewBox="0 0 24 24"><path d="M6.6 10.8a15 15 0 006.6 6.6l2.2-2.2a1 1 0 011-.25 11.4 11.4 0 003.6.57 1 1 0 011 1V20a1 1 0 01-1 1A17 17 0 013 4a1 1 0 011-1h3.5a1 1 0 011 1c0 1.25.2 2.45.57 3.57a1 1 0 01-.25 1z" fill="#f05a14"/></svg></div>
    <span>Phone : +1 555 010 2040</span>
  </div>
</div>
<div class="abs brand header-logo">velrato<span class="brand-dot"></span></div>
<nav class="abs nav">
  <a style="left:382px">Home</a><a style="left:491px">About</a><a style="left:606px">Services</a><a style="left:737px">Testimonials</a><a style="left:901px">Blog</a><a style="left:1004px">Contact us</a>
</nav>

<!-- hero -->
<section class="abs hero" role="img" aria-label="Photo of smiling colleagues gathered around a laptop in a bright office"></section>
<h1 class="abs hero-title">Welcome To<br>velrato</h1>
<p class="abs hero-text">Duis aute irure dolor in reprehenderit in voluptate velit esse.</p>
<div class="abs btn hero-btn">Get Started</div>
<svg class="abs hero-wave" width="1200" height="80" viewBox="0 0 1200 80">
  <path d="M0 48 C200 80 420 0 620 30 C820 58 1000 22 1200 60 V80 H0Z" fill="#fff"/>
  <path d="M0 48 C200 80 420 0 620 30 C820 58 1000 22 1200 60" fill="none" stroke="#f05a14" stroke-width="7"/>
</svg>

<!-- about -->
<svg class="abs about-photo" width="426" height="422" viewBox="0 0 426 422">
  <defs><linearGradient id="aboutFill" x1="0" y1="0" x2="1" y2="1"><stop offset="0" stop-color="#9b8d7e"/><stop offset=".5" stop-color="#4a4a50"/><stop offset="1" stop-color="#2b2e36"/></linearGradient></defs>
  <path role="img" aria-label="Photo of smiling coworkers seated at laptops" d="M180 4 C250-6 300 60 360 150 C420 240 440 330 380 390 C320 440 140 430 60 385 C-10 345-8 250 30 160 C70 70 120 12 180 4Z" fill="url(#aboutFill)" stroke="#f05a14" stroke-width="4"/>
</svg>
<h2 class="abs about-title">About <span class="accent">Velrato</span></h2>
<div class="abs about-text">
  <p>Nemo enim ipsam volupttem quia voluptas sit aspernatur aut odit aut fugit, sed quia consequuntur magni dolores eos qui ratione volutem sequi nescunt. Neque porro quiam est, qui drem ipsum quia dolor sit amet, consectetur, adipisci velit, sed quia non numquam eius modi tempora incidunt ut labore et dolore magnam.</p>
  <p>Ut enim ad minima veniam, quis nostrum exercitationem ullam corporis suscipit laboriosam, nisi ut aliquid ex ea commodi consequatur.</p>
</div>
<div class="abs btn about-btn">Read More</div>

<!-- services -->
<section class="abs services" role="img" aria-label="Orange-tinted photo of a team meeting in an office"></section>
<h2 class="abs sec-title services-title">Our Services</h2>
<p class="abs sec-title services-sub" style="font-weight:400">Sed ut perspiciatis unde omnis iste natus&nbsp; eaque ipsa quae ab illo inventore veritatis et<br>quasi architecto beatae vitae dicta sunt explicabo.</p>
<svg class="abs arrow" style="left:34px" width="32" height="20" viewBox="0 0 32 20"><path d="M31 10H2M10 2L2 10l8 8" fill="none" stroke="#fff" stroke-width="2.4"/></svg>
<svg class="abs arrow" style="left:1124px" width="32" height="20" viewBox="0 0 32 20"><path d="M1 10h29M22 2l8 8-8 8" fill="none" stroke="#fff" stroke-width="2.4"/></svg>
<article class="abs card" style="left:111px">
  <div class="card-photo" role="img" aria-label="Photo of a smiling professional woman in an office"></div>
  <h3>Finibus Bonorum</h3>
  <p>Itaque earum rerum hic tenetur a sapiente delectus, ut aut reiciendis voluptatibus maiores alias consequatur aut perferendis doloribus asperiores <b>Read More</b></p>
</article>
<article class="abs card" style="left:445px">
  <div class="card-photo" role="img" aria-label="Photo of a young woman with glasses in a yellow top" style="background:linear-gradient(160deg,#cfc8bf,#e2a62a)"></div>
  <h3>Dignissimos Ducimus</h3>
  <p>Itaque earum rerum hic tenetur a sapiente delectus, ut aut reiciendis voluptatibus maiores alias consequatur aut perferendis doloribus asperiores <b>Read More</b></p>
</article>
<article class="abs card" style="left:793px">
  <div class="card-photo" role="img" aria-label="Photo of a team applauding in a meeting" style="background:linear-gradient(160deg,#d7d4d0,#5c5e66)"></div>
  <h3>Blanditiis Praesent</h3>
  <p>Duis aute irure dolor in reprehenderit in voluptate velit esse cillum dolore eu fugiat nulla pariatur. Excepteur sint occaecat cupidatat non <b>Read More</b></p>
</article>

<!-- testimonials -->
<h2 class="abs sec-title t-title">What <span class="accent">Customer Says</span></h2>
<div class="abs t-quote"><svg width="28" height="22" viewBox="0 0 28 22"><path d="M2 12c0-6 4-10 9-11v4c-3 1-4 3-4 5h4v11H2zM16 12c0-6 4-10 9-11v4c-3 1-4 3-4 5h4v11h-9z" fill="#fff"/></svg></div>
<p class="abs sec-title t-name">Marten Oakes<span class="stars">★★★★★</span></p>
<p class="abs t-text">Lorem ipsum dolor sit amet, consectetur adipiscing elit, sed do eiusmod tempor incididunt ut labore et dolore magna aliqua. Ut enim ad minim veniam, quis nostrud exercitation ullamco laboris nisi ut aliquip ex ea commodo consequat fugiat nulla pariatur.</p>
<p class="abs sec-title t-thanks">Thanks, velrato</p>
<p class="abs t-side" style="left:-10px;width:200px;text-align:left">r aut odit aut fugit, sed eque porro quisquam oluptatem. Ut enim ad di consequatur</p>
<p class="abs t-side-name">Brielle</p>
<p class="abs t-side" style="left:1010px;width:220px;text-align:center">Nemo enim ipsam volu quia dolores eos qui r est, qui dolorem ipsum minima veniam</p>
<div class="abs dots"><span></span><span class="on"></span><span></span></div>

<!-- video -->
<section class="abs video-band" role="img" aria-label="Orange-tinted photo of colleagues in a casual workspace"></section>
<div class="abs video-frame" role="img" aria-label="Video still of a smiling woman working on a laptop beside a sofa">
  <div class="abs brand video-logo">velrato<span class="brand-dot"></span></div>
  <svg class="abs play" width="62" height="62" viewBox="0 0 62 62"><circle cx="31" cy="31" r="28" fill="#fff" stroke="#f05a14" stroke-width="5"/><path d="M24 18l20 13-20 13z" fill="#f05a14"/></svg>
</div>

<!-- contact -->
<h2 class="abs sec-title c-title"><span class="accent">Get</span> In Touch</h2>
<p class="abs sec-title c-sub">Nemo enim ipsam voluptatem quia voluptas sit aspernatur aut odit aut fugit, sed<br>quia consequuntur magni dolores eos qui ratione voluptatem sequi nesciunt.</p>
<div class="abs info-card">
  <h3>CONTACT INFO</h3>
  <div class="info-row" style="top:152px">
    <div class="info-ic"><svg width="16" height="18" viewBox="0 0 16 18"><path d="M8 17s6-6 6-10A6 6 0 002 7c0 4 6 10 6 10z" fill="none" stroke="#fff" stroke-width="1.6"/><circle cx="8" cy="7" r="2" fill="#fff"/></svg></div>
    <div><h4>ADDRESS</h4><p>Door No, 48 Harbor Lane<br>Fenwick Bay,US</p></div>
  </div>
  <div class="info-row" style="top:266px">
    <div class="info-ic"><svg width="16" height="16" viewBox="0 0 24 24"><path d="M6.6 10.8a15 15 0 006.6 6.6l2.2-2.2a1 1 0 011-.25 11.4 11.4 0 003.6.57 1 1 0 011 1V20a1 1 0 01-1 1A17 17 0 013 4a1 1 0 011-1h3.5a1 1 0 011 1c0 1.25.2 2.45.57 3.57a1 1 0 01-.25 1z" fill="#fff"/></svg></div>
    <div><h4>PHONE NO</h4><p>+1 555 010 2040</p></div>
  </div>
  <div class="info-row" style="top:360px">
    <div class="info-ic"><svg width="18" height="14" viewBox="0 0 18 14"><rect x="1" y="1" width="16" height="12" fill="none" stroke="#fff" stroke-width="1.6"/><path d="M1 1l8 7 8-7" fill="none" stroke="#fff" stroke-width="1.6"/></svg></div>
    <div><h4>EMAIL</h4><p>hello@velrato.com</p></div>
  </div>
</div>
<form class="abs msg">
  <h3>SEND A MESSAGE</h3>
  <div class="field">Full Name</div>
  <div class="field">Phone no</div>
  <div class="field tall">Address</div>
  <div class="submit">SUBMIT</div>
</form>

<!-- footer -->
<footer class="abs footer">
  <svg class="abs" style="left:0;top:0" width="1200" height="567" viewBox="0 0 1200 567">
    <path d="M0 20 C200 60 420 0 620 30 C820 60 1000 40 1200 10 V567 H0Z" fill="#000"/>
    <path d="M0 12 C200 52 420 -8 620 22 C820 52 1000 32 1200 2" fill="none" stroke="#f05a14" stroke-width="8"/>
  </svg>
</footer>
<h3 class="abs sub-title" style="font-weight:400">Subscribe for Join us</h3>
<div class="abs sub-form"><span>Enter Your Email</span><b>SUBSCRIBE</b></div>
<div class="abs f-rule"></div>
<div class="abs f-col" style="left:111px;width:240px">
  <h4 class="b">Contact</h4>
  <div class="f-item"><svg width="12" height="16" viewBox="0 0 16 18"><path d="M8 17s6-6 6-10A6 6 0 002 7c0 4 6 10 6 10z" fill="#fff"/><circle cx="8" cy="7" r="2" fill="#000"/></svg><span>12, Larkspur Street<br>Fenwick Bay, California</span></div>
  <div class="f-item"><svg width="13" height="13" viewBox="0 0 24 24"><path d="M6.6 10.8a15 15 0 006.6 6.6l2.2-2.2a1 1 0 011-.25 11.4 11.4 0 003.6.57 1 1 0 011 1V20a1 1 0 01-1 1A17 17 0 013 4a1 1 0 011-1h3.5a1 1 0 011 1c0 1.25.2 2.45.57 3.57a1 1 0 01-.25 1z" fill="#fff"/></svg><span>+1 555 010 2040</span></div>
  <div class="f-item"><svg width="14" height="11" viewBox="0 0 18 14"><rect x="0" y="0" width="18" height="14" fill="#fff"/><path d="M1 1l8 7 8-7" fill="none" stroke="#000" stroke-width="1.6"/></svg><span>info@velrato.com</span></div>
</div>
<div class="abs f-col" style="left:400px"><h4>Quick Links</h4><ul><li>Home</li><li>About</li><li>Services</li><li>Testimonials</li><li>Contact</li></ul></div>
<div class="abs f-col" style="left:652px"><h4>Help Center</h4><ul><li>FAQ</li><li>Terms</li><li>Privacy Policy</li><li>Support Center</li><li>Conditions</li></ul></div>
<div class="abs f-col" style="left:884px;width:205px">
  <h4>About velrato</h4>
  <p style="font-size:13.5px;line-height:1.7;text-align:justify">Excepteur sint occaecat cupidatat non proident, sunt in culpa qui officia deserunt</p>
  <p style="font-family:'Poppins',sans-serif;font-size:10px;font-weight:500;margin-top:4px">FOLLOW US ON:</p>
  <div class="f-soc"><span></span><span></span><span></span><span></span></div>
</div>
<div class="abs copy"><i></i><span>Copyrights@2022.velrato.All Rights Reserved</span><i></i></div>

</body>
</html>
```